Frostvale Harborline LLC

we need a business card design

Industry/Entity Type

hvac

Contact Information for Business Card

my logo

Requirements
Must have
• my logo and same colors

```html
<!DOCTYPE html>
<html lang="en">
<head>
<meta charset="utf-8">
<title>Frostvale Harborline LLC – Business Card</title>
<link rel="stylesheet" href="https://fonts.googleapis.com/css2?family=Montserrat:wght@400;500;700;800&display=swap">
<style>
  :root {
    --brand-blue: #1160ab;
    --deep-blue: #0f5aa6;
    --sky-blue: #1ba3e0;
    --gold: #f5b335;
    --white: #ffffff;
    --ink: #2a2a2a;
    --backdrop: #3a3a3a;
  }
  * { box-sizing: border-box; margin: 0; padding: 0; }
  html, body {
    width: 1200px; height: 875px; overflow: hidden;
    background: var(--backdrop);
    font-family: "Montserrat", sans-serif;
  }
  .canvas { position: relative; width: 1200px; height: 875px; }

  .card {
    position: absolute;
    width: 560px; height: 320px;
    border-radius: 18px;
    overflow: hidden;
  }

  /* Front */
  .card-front {
    left: 60px; top: 70px;
    background: var(--brand-blue);
    display: flex; align-items: center; justify-content: center;
  }
  .brand-lockup { display: flex; align-items: center; gap: 14px; }
  .brand-dot {
    width: 26px; height: 26px; border-radius: 50%;
    background: var(--gold);
    flex: none;
  }
  .brand-name {
    color: var(--white);
    font-weight: 800;
    font-size: 30px;
    line-height: 1.15;
    letter-spacing: 0.5px;
  }

  /* Back */
  .card-back {
    left: 580px; top: 480px;
    background: var(--white);
  }
  .card-back .brand-lockup {
    position: absolute; left: 34px; top: 92px; gap: 10px;
  }
  .card-back .brand-dot { width: 18px; height: 18px; }
  .card-back .brand-name {
    color: var(--brand-blue);
    font-size: 19px;
  }
  .divider {
    position: absolute; left: 272px; top: 40px;
    width: 2px; height: 140px;
    background: var(--gold);
  }
  .contact {
    position: absolute; left: 296px; top: 38px;
    color: var(--ink);
  }
  .person-name {
    font-weight: 800; font-size: 21px; letter-spacing: 0.3px;
    color: var(--brand-blue);
  }
  .person-name .surname { color: var(--sky-blue); }
  .person-role { font-size: 12.5px; margin-bottom: 10px; }
  .address { font-size: 11.5px; line-height: 1.45; margin-bottom: 8px; }
  .contact-list { list-style: none; font-size: 11.5px; line-height: 1.6; }
  .contact-list li { display: flex; align-items: center; gap: 7px; }
  .contact-list svg { width: 11px; height: 11px; flex: none; }

  .swoosh { position: absolute; left: 0; bottom: 0; width: 560px; height: 150px; }
</style>
</head>
<body>
<main class="canvas">

  <section class="card card-front" aria-label="Card front">
    <div class="brand-lockup">
      <span class="brand-dot"></span>
      <span class="brand-name">Frostvale<br>Harborline LLC</span>
    </div>
  </section>

  <section class="card card-back" aria-label="Card back">
    <div class="brand-lockup">
      <span class="brand-dot"></span>
      <span class="brand-name">Frostvale<br>Harborline LLC</span>
    </div>

    <div class="divider"></div>

    <div class="contact">
      <h1 class="person-name">DORIAN <span class="surname">WELK</span></h1>
      <p class="person-role">Founder</p>
      <p class="address">12/40 Upper Ridge Rd<br>Kelmoor XYZ 4120</p>
      <ul class="contact-list">
        <li>
          <svg viewBox="0 0 12 12" aria-hidden="true"><path d="M2.5 1 L4.5 1 L5.2 3.5 L4 4.5 Q5 7 7.5 8 L8.5 6.8 L11 7.5 L11 9.5 Q10.5 11 9 11 Q1 10 1 3 Q1 1.5 2.5 1Z" fill="var(--sky-blue)"/></svg>
          555.210.0483
        </li>
        <li>
          <svg viewBox="0 0 12 12" aria-hidden="true"><rect x="0.5" y="2" width="11" height="8" rx="1" fill="var(--sky-blue)"/><path d="M0.5 2.5 L6 6.5 L11.5 2.5" stroke="var(--white)" stroke-width="1" fill="none"/></svg>
          info@frostvaleharbor.com
        </li>
        <li>
          <svg viewBox="0 0 12 12" aria-hidden="true"><circle cx="6" cy="6" r="5" fill="none" stroke="var(--sky-blue)" stroke-width="1.2"/><ellipse cx="6" cy="6" rx="2.2" ry="5" fill="none" stroke="var(--sky-blue)" stroke-width="1"/><line x1="1" y1="6" x2="11" y2="6" stroke="var(--sky-blue)" stroke-width="1"/></svg>
          www.frostvaleharbor.com
        </li>
      </ul>
    </div>

    <svg class="swoosh" viewBox="0 0 560 150" preserveAspectRatio="none" aria-hidden="true">
      <path d="M0 100 Q300 70 560 0 L560 150 L0 150Z" fill="var(--deep-blue)"/>
      <path d="M0 108 Q260 86 470 40" stroke="var(--gold)" stroke-width="5" fill="none"/>
      <path d="M250 88 Q430 60 560 -2" stroke="var(--sky-blue)" stroke-width="5" fill="none"/>
    </svg>
  </section>

</main>
</body>
</html>
```